SaaS Early tech startup business card design

Unique design for experience ecommerce platform company. the business cards will be used by executive members. conformance with color code is required.

```html
<!DOCTYPE html>
<html lang="en">
<head>
<meta charset="utf-8">
<title>Lumio Business Card</title>
<link href="https://fonts.googleapis.com/css2?family=Lato:wght@400;700;900&display=swap" rel="stylesheet">
<style>
  :root {
    --backdrop: #e3e3e3;
    --deep-blue: #08648f;
    --sea-green: #03b29a;
    --teal-text: #0e8fa0;
    --ink: #2d2d2d;
    --paper: #ffffff;
    --logo-light: #eaf8f5;
  }
  * { margin: 0; padding: 0; box-sizing: border-box; }
  html, body {
    width: 1200px; height: 900px; overflow: hidden;
    background: var(--backdrop);
    font-family: "Lato", sans-serif;
  }
  .card {
    position: absolute;
    top: 217px;
    width: 309px; height: 500px;
    box-shadow: 3px 3px 4px rgba(0,0,0,0.35);
  }
  .card-back {
    left: 279px;
    border-radius: 0 66px 0 66px;
    background: linear-gradient(to bottom, var(--deep-blue), var(--sea-green));
    display: flex; align-items: center; justify-content: center;
  }
  .card-front {
    left: 617px;
    border-radius: 66px 0 66px 0;
    background: var(--paper);
  }
  .brand-name {
    font-family: "Lato", sans-serif;
    font-weight: 900;
    font-size: 84px;
    letter-spacing: -1px;
    line-height: 1;
  }
  .card-back .brand-name { color: var(--logo-light); margin-bottom: 6px; }
  .card-front .brand-name {
    position: absolute; left: 36px; top: 300px; margin-top: -228px;
    color: var(--teal-text);
  }
  .person {
    position: absolute; left: 37px; top: 293px;
  }
  .person-name {
    font-weight: 700; font-size: 18.5px; color: var(--teal-text);
    letter-spacing: 0.2px; line-height: 1.1;
  }
  .person-role {
    font-size: 14.5px; color: var(--ink); line-height: 1.2;
  }
  .contact-list {
    position: absolute; left: 36px; top: 344px; list-style: none;
  }
  .contact-list li {
    display: flex; align-items: center; gap: 5px;
    font-size: 14px; color: var(--ink); height: 19px;
  }
  .contact-list svg { width: 15px; height: 15px; flex: none; fill: none; stroke: var(--teal-text); stroke-width: 1.8; }
  .address {
    position: absolute; left: 38px; top: 419px;
    display: flex; gap: 5px;
    font-size: 14px; color: var(--ink); line-height: 18px;
  }
  .address svg { width: 12px; height: 16px; flex: none; margin-top: 1px; }
</style>
</head>
<body>
  <section class="card card-back">
    <span class="brand-name">lumio</span>
  </section>

  <section class="card card-front">
    <span class="brand-name">lumio</span>

    <div class="person">
      <p class="person-name">DANIEL MORENO</p>
      <p class="person-role">Managing Director</p>
    </div>

    <ul class="contact-list">
      <li>
        <svg viewBox="0 0 24 24"><path d="M5 3l4 1 1 5-2 1.5a12 12 0 0 0 6 6L15.5 14l5 1 1 4-2 2C11 21 3 13 3 5z"/><path d="M14 3a7 7 0 0 1 7 7M14 7a3 3 0 0 1 3 3"/></svg>
        044-987 654 321
      </li>
      <li>
        <svg viewBox="0 0 24 24"><rect x="2" y="5" width="20" height="14" fill="#0e8fa0"/><path d="M2 5l10 8 10-8M2 19l7-7M22 19l-7-7" stroke="#fff"/></svg>
        hello@lumiohq.com
      </li>
      <li>
        <svg viewBox="0 0 24 24"><circle cx="12" cy="12" r="10"/><ellipse cx="12" cy="12" rx="4" ry="10"/><path d="M2 12h20M4 7h16M4 17h16"/></svg>
        www.lumiohq.com
      </li>
    </ul>

    <div class="address">
      <svg viewBox="0 0 12 16"><path d="M6 0a6 6 0 0 0-6 6c0 4 6 10 6 10s6-6 6-10a6 6 0 0 0-6-6z" fill="#0e8fa0"/><circle cx="6" cy="6" r="2.2" fill="#fff"/></svg>
      <p>18, Harbour Street<br>Northfield, 30917</p>
    </div>
  </section>
</body>
</html>
```